Business Card Design for Training Business

Clear Path Coaching is a new business that delivers training and other services with a focus on topics related to mental health and wellbeing, for example, Wellmind Response Course, Resilience etc. We have a strong focus on evidence-based psychology and neuroscience. I have a logo which I will upload with the brief, so please consider colours that work well with the logo.
Target Market(s)
Adults, workplaces (particularly government and not-for-profits)
Industry/Entity Type
Business
Contact Information for Business Card
Head Strong TrainingSamantha SellwoodDirector0438 770 850sam@headstrongtraining.com.auwww.headstrongtraining.com.au

```html
<!DOCTYPE html>
<html lang="en">
<head>
<meta charset="utf-8">
<title>Clear Path Coaching – Business Card</title>
<link rel="stylesheet" href="https://fonts.googleapis.com/css2?family=Questrial&display=swap">
<style>
  :root {
    --page-bg: #e4e1dc;
    --teal-light: #3cc3c0;
    --teal-mid: #17a3a5;
    --teal-deep: #0a747c;
    --frost: #eef0ee;
    --frost-edge: #d9dedc;
    --ring: #2a2324;
    --brand-ink: #3a3d40;
    --brand-accent: #1a9ea3;
    --contact-ink: #f6ecea;
    --name-ink: #ffffff;
  }
  * { margin: 0; padding: 0; box-sizing: border-box; }
  html, body {
    width: 1200px;
    height: 969px;
    overflow: hidden;
    background: var(--page-bg);
    font-family: "Questrial", "Century Gothic", sans-serif;
  }
  .card {
    position: absolute;
    left: 100px;
    top: 201px;
    width: 1000px;
    height: 567px;
    overflow: hidden;
    background:
      radial-gradient(ellipse at 20% 10%, var(--teal-light) 0%, transparent 60%),
      linear-gradient(180deg, var(--teal-mid) 0%, var(--teal-deep) 100%);
    box-shadow: 0 18px 40px rgba(0, 0, 0, 0.18);
  }
  .card__disc {
    position: absolute;
    left: 0;
    top: 0;
    width: 1000px;
    height: 567px;
  }
  .brand {
    position: absolute;
    left: 560px;
    top: 72px;
    width: 420px;
    text-align: center;
  }
  .brand__dot {
    display: block;
    width: 112px;
    height: 112px;
    margin: 0 auto 30px;
    border: 3px solid var(--brand-accent);
    border-radius: 50%;
  }
  .brand__name {
    font-size: 34px;
    letter-spacing: 3px;
    line-height: 1.25;
    color: var(--brand-ink);
    text-transform: uppercase;
  }
  .person {
    position: absolute;
    left: 55px;
    top: 312px;
    color: var(--name-ink);
  }
  .person__name {
    font-size: 34px;
    letter-spacing: 0.5px;
  }
  .person__role {
    font-size: 25px;
    margin-top: 2px;
    opacity: 0.9;
  }
  .contact {
    position: absolute;
    left: 55px;
    top: 416px;
    list-style: none;
    color: var(--contact-ink);
    font-size: 23px;
  }
  .contact__item {
    display: flex;
    align-items: center;
    height: 38.5px;
  }
  .contact__icon {
    width: 22px;
    height: 22px;
    margin-right: 14px;
    fill: var(--contact-ink);
  }
</style>
</head>
<body>
  <section class="card" aria-label="Clear Path Coaching business card">
    <svg class="card__disc" viewBox="0 0 1000 567" aria-hidden="true">
      <defs>
        <radialGradient id="frostFill" cx="0.45" cy="0.45" r="0.6">
          <stop offset="0" stop-color="#f6f7f5"/>
          <stop offset="1" stop-color="#dde2e0"/>
        </radialGradient>
      </defs>
      <circle cx="791" cy="149" r="373" fill="url(#frostFill)" stroke="var(--ring)" stroke-width="7"/>
    </svg>

    <div class="brand">
      <span class="brand__dot" aria-hidden="true"></span>
      <p class="brand__name">Clear Path<br>Coaching</p>
    </div>

    <div class="person">
      <h1 class="person__name">Rebecca Tanfield</h1>
      <p class="person__role">Director</p>
    </div>

    <ul class="contact">
      <li class="contact__item">
        <svg class="contact__icon" viewBox="0 0 24 24" aria-hidden="true"><path d="M6.6 10.8a15.1 15.1 0 0 0 6.6 6.6l2.2-2.2c.3-.3.7-.4 1-.2 1.1.4 2.3.6 3.6.6.6 0 1 .4 1 1V20c0 .6-.4 1-1 1A17 17 0 0 1 3 4c0-.6.4-1 1-1h3.5c.6 0 1 .4 1 1 0 1.3.2 2.5.6 3.6.1.3 0 .7-.2 1z"/></svg>
        <span>0491 362 517</span>
      </li>
      <li class="contact__item">
        <svg class="contact__icon" viewBox="0 0 24 24" aria-hidden="true"><path d="M2 5h20v14H2z M3.5 6.5v.4l8.5 5.6 8.5-5.6v-.4z" fill-rule="evenodd"/></svg>
        <span>bec@clearpathcoaching.example.au</span>
      </li>
      <li class="contact__item">
        <svg class="contact__icon" viewBox="0 0 24 24" aria-hidden="true"><path d="M12 2a10 10 0 1 0 0 20 10 10 0 0 0 0-20zm0 2c.9 0 2.2 1.9 2.8 5H9.2C9.8 5.9 11.1 4 12 4zM4.3 11h3a20 20 0 0 0 0 2h-3a8 8 0 0 1 0-2zm4.9 0h5.6a18 18 0 0 1 0 2H9.2a18 18 0 0 1 0-2zm7.5 0h3a8 8 0 0 1 0 2h-3a20 20 0 0 0 0-2zM12 20c-.9 0-2.2-1.9-2.8-5h5.6c-.6 3.1-1.9 5-2.8 5z"/></svg>
        <span>www.clearpathcoaching.example.au</span>
      </li>
    </ul>
  </section>
</body>
</html>
```